Core Values Poster for Technology Business

A core values poster for our office. We don't have much in mind beyond a couple of logos (we have two companies) and then the 4 Core Values we want to present. Mostly, we want this to be simple (easy to take in as a reminder in 5-10 seconds) in a very visually appealing way.

If you can incorporate a high-look-and-feel, great, but not if it over complicates the entire poster/sign.

The core values are:
Relationships Matter
Passion Drives us to Excellence
All About Teamwork
Consistent, Resourceful, Relentless

Our file with both logos together is attached. This is a low-res version. We would provide a high-res version for final production.

Industry/Entity Type

Business

Font styles to use
Serif

Colors
ec1f27
0255a3

Requirements
Nice to have
• This is an update. To be able to incorporate some of our corporate look-and-feel, but not have a black background (as on our kolabrite.net stie), please see the Video Conferencing Slick file that I have uploaded. Might be able to use parts of this type of format to tie in (but not use it exactly as-is - since this is a client facing document).

```html
<!DOCTYPE html>
<html lang="en">
<head>
<meta charset="utf-8">
<title>Core Values Poster</title>
<link href="https://fonts.googleapis.com/css2?family=Bebas+Neue&display=swap" rel="stylesheet">
<style>
  :root {
    --page: #ffffff;
    --ink: #111111;
    --night: #0b0b0b;
    --paper: #ffffff;
    --rose: #e8335f;
    --steel: #2f79ad;
    --lamp: #f3ec9a;
    --logo-grey: #3a3a3a;
    --logo-blue: #3b4f8c;
  }
  * { margin: 0; padding: 0; box-sizing: border-box; }
  html, body { width: 1200px; height: 1000px; overflow: hidden; background: var(--page); }
  body { position: relative; font-family: "Bebas Neue", "Oswald", sans-serif; }

  .poster { position: absolute; top: 115px; width: 478px; height: 703px; overflow: hidden; }
  .poster--dark { left: 103px; }
  .poster--light { left: 620px; }
  .poster__frame { position: absolute; inset: 0; width: 478px; height: 703px; }

  .brand { position: absolute; color: var(--logo-grey); white-space: nowrap; display: flex; align-items: center; gap: 5px; line-height: 1; }
  .brand--primary { left: 14px; top: 12px; font-size: 24px; }
  .brand--primary .brand__dot { width: 12px; height: 12px; border-radius: 50%; background: var(--rose); }
  .brand--secondary { left: 295px; top: 19px; font-size: 19px; color: var(--logo-blue); }
  .brand--secondary .brand__dot { width: 10px; height: 10px; background: var(--rose); }

  .value { position: absolute; white-space: nowrap; line-height: 1; color: var(--paper); letter-spacing: 0.03em; }
  .value .sc { font-size: 0.8em; }
  .value--relationships { left: 112px; top: 222px; font-size: 78px; }
  .value--matter { left: 115px; top: 291px; font-size: 33px; letter-spacing: 0.5em; }
  .value--passion { left: 47px; top: 326px; font-size: 46px; }
  .value--excellence { left: 47px; top: 360px; font-size: 68px; letter-spacing: 0.05em; }
  .value--allabout { left: 137px; top: 432px; font-size: 38px; letter-spacing: 0.48em; }
  .value--teamwork { left: 137px; top: 463px; font-size: 73px; letter-spacing: 0.05em; }
  .value--trio { left: 52px; top: 535px; font-size: 64px; line-height: 50px; letter-spacing: 0; }

  .icon { position: absolute; border-radius: 10px; background: var(--paper); opacity: 0.9; }
  .icon--hearts { left: 25px; top: 262px; width: 80px; height: 40px; border-radius: 20px; }
  .icon--partner { left: 359px; top: 343px; width: 96px; height: 70px; }
  .icon--team { left: 42px; top: 455px; width: 90px; height: 72px; }
  .icon--process { left: 320px; top: 550px; width: 125px; height: 116px; border-radius: 50%; }

  .poster--light .value--relationships,
  .poster--light .value--matter,
  .poster--light .value--allabout,
  .poster--light .value--teamwork { color: var(--rose); }
  .poster--light .value--passion,
  .poster--light .value--excellence,
  .poster--light .value--trio { color: var(--steel); }
  .poster--light .icon--hearts,
  .poster--light .icon--team { background: var(--rose); }
  .poster--light .icon--partner,
  .poster--light .icon--process { background: var(--steel); }
  .poster--light .icon--partner { left: 362px; top: 337px; width: 72px; height: 76px; }

  .caption { position: absolute; top: 852px; width: 478px; text-align: center; font-size: 44px; color: var(--ink); line-height: 1; }
  .caption .sc { font-size: 0.8em; }
  .caption--dark { left: 103px; }
  .caption--light { left: 620px; }
</style>
</head>
<body>

<section class="poster poster--dark">
  <svg class="poster__frame" viewBox="0 0 478 703" aria-hidden="true">
    <defs>
      <linearGradient id="fade-dark" x1="0" y1="0" x2="0" y2="1">
        <stop offset="0" stop-color="#ffffff"/>
        <stop offset="0.08" stop-color="#ffffff"/>
        <stop offset="0.15" stop-color="#0b0b0b"/>
        <stop offset="1" stop-color="#0b0b0b"/>
      </linearGradient>
    </defs>
    <rect width="478" height="703" fill="url(#fade-dark)"/>
    <path d="M0,95 Q239,45 478,95 L478,110 Q239,60 0,110 Z" fill="var(--rose)"/>
    <path d="M0,112 Q239,62 478,112 L478,185 Q239,140 0,185 Z" fill="var(--steel)"/>
    <path d="M0,190 Q239,148 478,190 L478,222 Q239,180 0,222 Z" fill="var(--rose)"/>
    <circle cx="75" cy="140" r="8" fill="var(--lamp)"/>
    <circle cx="403" cy="140" r="8" fill="var(--lamp)"/>
    <text x="239" y="160" text-anchor="middle" fill="#fff" font-family="Bebas Neue, sans-serif" font-size="74">C<tspan font-size="60">ORE</tspan> V<tspan font-size="60">ALUES</tspan></text>
  </svg>
  <div class="brand brand--primary"><span class="brand__dot"></span>Quorvane</div>
  <div class="brand brand--secondary"><span class="brand__dot"></span>Sentinel Guard Group</div>

  <div class="icon icon--hearts" role="img" aria-label="Two linked hearts icon"></div>
  <p class="value value--relationships">R<span class="sc">ELATIONSHIPS</span></p>
  <p class="value value--matter">MATTER</p>
  <div class="icon icon--partner" role="img" aria-label="Handshake icon"></div>
  <p class="value value--passion">P<span class="sc">ASSION</span> D<span class="sc">RIVES US TO</span></p>
  <p class="value value--excellence">EXCELLENCE</p>
  <div class="icon icon--team" role="img" aria-label="Two teammates raising a trophy icon"></div>
  <p class="value value--allabout">ALL ABOUT</p>
  <p class="value value--teamwork">TEAMWORK</p>
  <div class="icon icon--process" role="img" aria-label="Team, growth chart and gear icon cluster"></div>
  <p class="value value--trio">CONSISTENT<br>RESOURCEFUL<br>RELENTLESS</p>
</section>

<section class="poster poster--light">
  <svg class="poster__frame" viewBox="0 0 478 703" aria-hidden="true">
    <defs>
      <linearGradient id="fade-light" x1="0" y1="0" x2="0" y2="1">
        <stop offset="0" stop-color="#ffffff"/>
        <stop offset="0.08" stop-color="#ffffff"/>
        <stop offset="0.15" stop-color="#0b0b0b"/>
        <stop offset="1" stop-color="#0b0b0b"/>
      </linearGradient>
    </defs>
    <rect width="478" height="703" fill="url(#fade-light)"/>
    <path d="M0,95 Q239,45 478,95 L478,110 Q239,60 0,110 Z" fill="var(--rose)"/>
    <path d="M0,112 Q239,62 478,112 L478,185 Q239,140 0,185 Z" fill="var(--steel)"/>
    <path d="M0,190 Q239,148 478,190 L478,222 Q239,180 0,222 Z" fill="var(--rose)"/>
    <path d="M20,232 Q239,175 458,232 L458,683 L20,683 Z" fill="var(--paper)" stroke="var(--rose)" stroke-width="3"/>
    <circle cx="75" cy="140" r="8" fill="var(--lamp)"/>
    <circle cx="403" cy="140" r="8" fill="var(--lamp)"/>
    <text x="239" y="160" text-anchor="middle" fill="#fff" font-family="Bebas Neue, sans-serif" font-size="74">C<tspan font-size="60">ORE</tspan> V<tspan font-size="60">ALUES</tspan></text>
  </svg>
  <div class="brand brand--primary"><span class="brand__dot"></span>Quorvane</div>
  <div class="brand brand--secondary"><span class="brand__dot"></span>Sentinel Guard Group</div>

  <div class="icon icon--hearts" role="img" aria-label="Two linked hearts icon"></div>
  <p class="value value--relationships">R<span class="sc">ELATIONSHIPS</span></p>
  <p class="value value--matter">MATTER</p>
  <div class="icon icon--partner" role="img" aria-label="Trophy held on an open hand icon"></div>
  <p class="value value--passion">P<span class="sc">ASSION</span> D<span class="sc">RIVES US TO</span></p>
  <p class="value value--excellence">EXCELLENCE</p>
  <div class="icon icon--team" role="img" aria-label="Two teammates raising a trophy icon"></div>
  <p class="value value--allabout">ALL ABOUT</p>
  <p class="value value--teamwork">TEAMWORK</p>
  <div class="icon icon--process" role="img" aria-label="Team, growth chart and gear icon cluster"></div>
  <p class="value value--trio">CONSISTENT<br>RESOURCEFUL<br>RELENTLESS</p>
</section>

<p class="caption caption--dark">B<span class="sc">LACK AND</span> W<span class="sc">HITE</span> V<span class="sc">ERSION</span></p>
<p class="caption caption--light">B<span class="sc">LUE</span>, R<span class="sc">ED</span> , W<span class="sc">HITE</span> V<span class="sc">ERSION</span></p>

</body>
</html>
```